BrivoTerna. Lantern of the Steady Harvest. Business card

Professional business card for BrivoTerna (Lantern of the Steady Harvest)
My rationale: Strategy-> Execution-> Results-> Value that lead to the BrivoTerna name: We put the Lantern of the Steady Harvest.
We deliver value to our customers helping them at defining a good strategy (cyan arrow). 90% of well formulated strategies fail due to poor execution so we also consider strategical execution very important (green arrow). Due to the execution we obtain the results (blue arrow). Finally, the results provide feedback to redefine strategy, and the new strategy has to be executed and new results obtained providing new feedback and on and on. It's like a wheel that finally, must create corporate value: value for shareholders, staholders, employees, providers...-

Target Market(s)

CEOs and steering comitees , invewrnent funds

Industry/Entity Type

Business Consultant

Contact Information for Business Card

Teodoro Vinsquel
CEO & Founder
teodoro.vinsquel@brivoterna-example.com
Mobile: +34 655.803.912
www.brivoterna-example.com

Colors

Designer to choose colors to be used in the design.

Requirements
Nice to have
• Nice to hace the words: Strategy, execution, results
• Nice to vave the claim: Lantern of the Steady Harvest
• The three colors should be shown:
• cyan for STRATEGY
• green for EXECUTION
• blue for RESULTS
Should not have
• Complete black background

```html
<!DOCTYPE html>
<html lang="en">
<head>
<meta charset="utf-8">
<title>BrivoTerna – Business Card</title>
<link rel="stylesheet" href="https://fonts.googleapis.com/css2?family=Open+Sans:wght@400;600;700;800&display=swap">
<style>
  :root {
    --navy: #1f3c8f;
    --green: #8cc63f;
    --cyan: #29a8e0;
    --card: #ffffff;
    --bg-light: #e6e8ea;
    --bg-dark: #b9bcbf;
  }
  * { box-sizing: border-box; margin: 0; padding: 0; }
  html, body { width: 1200px; height: 800px; overflow: hidden; }
  body {
    font-family: "Open Sans", sans-serif;
    background: linear-gradient(135deg, var(--bg-light) 0%, var(--bg-dark) 100%);
    position: relative;
  }
  .card {
    position: absolute;
    left: 340px;
    width: 520px;
    height: 297px;
    background: var(--card);
    box-shadow: 0 6px 18px rgba(0,0,0,0.22);
    overflow: hidden;
  }
  .card--front { top: 70px; }
  .card--back { top: 423px; }

  /* Front */
  .front__brand {
    position: absolute;
    top: 96px; left: 0; right: 0;
    text-align: center;
    font-weight: 800;
    font-size: 52px;
    letter-spacing: -1px;
    color: var(--navy);
  }
  .front__claim {
    position: absolute;
    top: 178px; left: 0; right: 0;
    text-align: center;
    font-weight: 700;
    font-size: 13.5px;
    letter-spacing: 0.4px;
    text-transform: uppercase;
  }
  .claim--navy { color: var(--navy); }
  .claim--green { color: var(--green); }
  .claim--cyan { color: var(--cyan); }
  .front__bands {
    position: absolute;
    bottom: 0; left: 0; right: 0;
    height: 12px;
    display: flex;
  }
  .band { flex: 1; }
  .band--navy { background: var(--navy); }
  .band--green { background: var(--green); }
  .band--cyan { background: var(--cyan); }

  /* Back */
  .pillars {
    position: absolute;
    top: 70px; left: 36px;
    display: flex;
    flex-direction: column;
    gap: 14px;
    font-weight: 700;
    font-size: 26px;
    letter-spacing: 4px;
    text-transform: uppercase;
  }
  .pillar--results { color: var(--navy); }
  .pillar--execution { color: var(--green); }
  .pillar--strategy { color: var(--cyan); }

  .back__brand {
    position: absolute;
    top: 30px; right: 30px;
    font-weight: 800;
    font-size: 38px;
    letter-spacing: -0.8px;
    color: var(--navy);
  }
  .person {
    position: absolute;
    top: 122px; right: 30px;
    text-align: right;
  }
  .person__name {
    font-weight: 700;
    font-size: 17px;
    color: var(--navy);
  }
  .person__role {
    font-size: 14px;
    color: var(--cyan);
  }
  .contact {
    position: absolute;
    bottom: 26px; right: 30px;
    list-style: none;
    text-align: right;
    font-size: 13.5px;
    line-height: 21px;
    color: var(--navy);
  }
  .contact__item {
    display: flex;
    justify-content: flex-end;
    align-items: center;
    gap: 7px;
  }
  .contact__icon { width: 14px; height: 14px; flex: none; }
</style>
</head>
<body>

  <section class="card card--front" aria-label="Business card front">
    <div class="front__brand">BrivoTerna</div>
    <div class="front__claim">
      <span class="claim--navy">Lantern of the</span>
      <span class="claim--green">Steady</span>
      <span class="claim--cyan">Harvest</span>
    </div>
    <div class="front__bands">
      <div class="band band--navy"></div>
      <div class="band band--green"></div>
      <div class="band band--cyan"></div>
    </div>
  </section>

  <section class="card card--back" aria-label="Business card back">
    <div class="pillars">
      <span class="pillar--results">Results</span>
      <span class="pillar--execution">Execution</span>
      <span class="pillar--strategy">Strategy</span>
    </div>

    <div class="back__brand">BrivoTerna</div>

    <div class="person">
      <div class="person__name">Teodoro Vinsquel</div>
      <div class="person__role">CEO &amp; Founder</div>
    </div>

    <ul class="contact">
      <li class="contact__item">+34 655.803.912
        <svg class="contact__icon" viewBox="0 0 14 14" aria-hidden="true">
          <rect x="3.5" y="0.8" width="7" height="12.4" rx="1.3" fill="none" stroke="#8cc63f" stroke-width="1.3"/>
          <line x1="6" y1="11" x2="8" y2="11" stroke="#8cc63f" stroke-width="1.2"/>
        </svg>
      </li>
      <li class="contact__item">teodoro.vinsquel@brivoterna-example.com
        <svg class="contact__icon" viewBox="0 0 14 14" aria-hidden="true">
          <rect x="0.8" y="2.8" width="12.4" height="8.4" fill="none" stroke="#8cc63f" stroke-width="1.3"/>
          <polyline points="1,3 7,8 13,3" fill="none" stroke="#8cc63f" stroke-width="1.3"/>
        </svg>
      </li>
      <li class="contact__item">www.brivoterna-example.com
        <svg class="contact__icon" viewBox="0 0 14 14" aria-hidden="true">
          <circle cx="7" cy="7" r="6" fill="none" stroke="#8cc63f" stroke-width="1.3"/>
          <ellipse cx="7" cy="7" rx="2.6" ry="6" fill="none" stroke="#8cc63f" stroke-width="1"/>
          <line x1="1" y1="7" x2="13" y2="7" stroke="#8cc63f" stroke-width="1"/>
        </svg>
      </li>
    </ul>
  </section>

</body>
</html>
```